Whiskey label

I have an existing logo that I currently use for our moonshine and would like to create a similar design for our new whiskey product. We have other products check out our website www.hadleysstillhouse.com. Looking to release a new product with a similar design label so the public can relate it to our other products but different enough so it stands out from the competition

Target Market(s)

Male and Female 21+

Industry/Entity Type

Product

Logo Text

Rusty Hadley's Sovereign Whiskey

Colors

Designer to choose colors to be used in the design.

Requirements
Must have
• Image of man in chair either photo or something similar to that on our moonshine label. Country theme
Nice to have
• a label design that will stand out from the competition

```html
<!DOCTYPE html>
<html lang="en">
<head>
<meta charset="utf-8">
<title>Rusty Hadley's Sovereign Whiskey Label</title>
<link href="https://fonts.googleapis.com/css2?family=Rye&family=Alfa+Slab+One&family=Old+Standard+TT:wght@700&family=Arimo:wght@700&display=swap" rel="stylesheet">
<style>
  :root {
    --ink: #111111;
    --paper: #ffffff;
    --art-light: #dcdcdc;
    --art-dark: #707070;
    --band-edge: #3a3a3a;
  }
  html, body {
    margin: 0;
    padding: 0;
    width: 1200px;
    height: 1200px;
    overflow: hidden;
    background: var(--paper);
  }
  .canvas {
    position: relative;
    width: 1200px;
    height: 1200px;
  }
  .label {
    position: absolute;
    left: 290px;
    top: 100px;
    width: 620px;
    height: 1000px;
  }
  .brand-name { font-family: "Rye", serif; fill: var(--ink); }
  .headline { font-family: "Alfa Slab One", serif; fill: var(--ink); }
  .spec { font-family: "Old Standard TT", serif; font-weight: 700; fill: var(--ink); }
  .ribbon-text { font-family: "Arimo", sans-serif; font-weight: 700; fill: var(--ink); letter-spacing: 1px; }
  .origin-line { font-family: "Arimo", sans-serif; font-weight: 700; fill: var(--ink); }
  .abv-text { font-family: "Old Standard TT", serif; font-weight: 700; fill: var(--paper); }
  .frame-line { fill: none; stroke: var(--ink); }
  .panel { fill: var(--paper); stroke: var(--ink); }
</style>
</head>
<body>
<main class="canvas">
  <svg class="label" viewBox="0 0 372 600" xmlns="http://www.w3.org/2000/svg">
    <defs>
      <linearGradient id="portraitTone" x1="0" y1="0" x2="0" y2="1">
        <stop offset="0" stop-color="var(--art-dark)"/>
        <stop offset="1" stop-color="var(--art-light)"/>
      </linearGradient>
      <linearGradient id="bandTone" x1="0" y1="0" x2="1" y2="0">
        <stop offset="0" stop-color="var(--band-edge)"/>
        <stop offset="0.5" stop-color="var(--ink)"/>
        <stop offset="1" stop-color="var(--band-edge)"/>
      </linearGradient>
    </defs>

    <!-- outer frame -->
    <rect class="frame-line" x="3" y="24" width="366" height="480" stroke-width="4"/>
    <rect class="frame-line" x="11" y="32" width="350" height="464" stroke-width="1.2"/>

    <!-- arched name panel -->
    <path class="panel" stroke-width="2.5"
          d="M24 96 L24 40 Q186 -8 348 40 L348 96 Z"/>
    <path class="frame-line" stroke-width="1"
          d="M30 90 L30 44 Q186 -1 342 44 L342 90 Z"/>
    <text class="brand-name" x="186" y="78" text-anchor="middle" font-size="32"
          textLength="290" lengthAdjust="spacingAndGlyphs">RUSTY HADLEY'S</text>

    <!-- portrait illustration area -->
    <rect x="78" y="100" width="216" height="288" fill="url(#portraitTone)"
          role="img" aria-label="Illustration of a man seated in a wooden chair with arms crossed"/>

    <!-- side spec panels -->
    <rect class="panel" x="14" y="405" width="60" height="56" stroke-width="2"/>
    <rect class="panel" x="298" y="405" width="60" height="56" stroke-width="2"/>
    <text class="spec" x="44" y="432" text-anchor="middle" font-size="18">100</text>
    <text class="spec" x="44" y="447" text-anchor="middle" font-size="9" letter-spacing="0.5">PROOF</text>
    <text class="spec" x="328" y="432" text-anchor="middle" font-size="18">750</text>
    <text class="spec" x="328" y="447" text-anchor="middle" font-size="9" letter-spacing="0.5">ML</text>

    <!-- title block -->
    <rect class="panel" x="72" y="398" width="228" height="70" stroke-width="2.5"/>
    <rect class="panel" x="112" y="386" width="148" height="22" stroke-width="2"/>
    <text class="ribbon-text" x="186" y="402" text-anchor="middle" font-size="12">AUTHENTIC</text>
    <text class="headline" x="186" y="456" text-anchor="middle" font-size="38"
          textLength="204" lengthAdjust="spacingAndGlyphs">SOVEREIGN</text>

    <rect class="panel" x="60" y="474" width="252" height="62" stroke-width="2.5"/>
    <line x1="96" y1="474" x2="176" y2="474" stroke="var(--ink)" stroke-width="1"/>
    <circle cx="186" cy="474" r="3.5" fill="var(--paper)" stroke="var(--ink)" stroke-width="1"/>
    <line x1="196" y1="474" x2="276" y2="474" stroke="var(--ink)" stroke-width="1"/>
    <text class="headline" x="186" y="520" text-anchor="middle" font-size="36"
          textLength="224" lengthAdjust="spacingAndGlyphs">WHISKEY</text>

    <!-- origin and strength -->
    <text class="origin-line" x="186" y="556" text-anchor="middle" font-size="9"
          textLength="296" lengthAdjust="spacingAndGlyphs">Bottled and Distilled in Pine Hollow, North Carolina</text>
    <path d="M66 566 L306 566 Q311 576 306 586 L66 586 Q61 576 66 566 Z" fill="url(#bandTone)"/>
    <text class="abv-text" x="186" y="581" text-anchor="middle" font-size="13">50% ALC/VOL</text>
  </svg>
</main>
</body>
</html>
```